Business card for Crestline Bathrooms

Please design a business card for our bathroom renovation business. You can use my existing logo, but if you have an idea to modernize it, I would like to see it. Please see attached files first. I would like to use the blue and the orange theme. I like the concept of using the shower head in the logo. Please find following a design (or two) that I have been trying to create with my limited resources. That design was for a sign, but I was going to adopt it and use it as a business card as well. I like the concept of the water splash but I don’t think it “flows” nicely together with the logo. Another thought is that maybe creating the logo out of water splash could work and have a dramatic effect (like the water text and the butterfly picture attached with similar background instead of white). If the above doesn’t work I would like to see a modern simplified design. One of the attached files named as the unwanted business card has all the details that I want included in the business card. Please note that it is two sided.
Updates

I am very thankful for the designs that I have received, but they are very similar and only a couple of attempts to do something with the water splash as per my original brief. Modernizing the logo and having it made out of out of water splash with the orange as color accent could work and have a dramatic effect (like the water text and the butterfly picture attached with similar background instead of white). Please do not use the butterfly itself! This is just an example that images can be created out of water splash.

Contact Information for Business Card

all the details are on the unwonted business card file included

Colors
3176b5

Requirements
Nice to have
• Copied from the brief:
• ... maybe creating the logo out of water splash could work and have a dramatic effect (like the water text and the butterfly picture attached with similar background instead of white). Please do not use the butterfly itself!
Should not have
• I am getting designs with a butterfly. The butterfly picture was an example of creating something from a water splash. The butterfly itself has no association with anything other than the concept of creating a logo out of water splash. Sorry, I thought I was clear in the brief.

```html
<!DOCTYPE html>
<html lang="en">
<head>
<meta charset="utf-8">
<title>Crestline Bathrooms – Business Card</title>
<link rel="stylesheet" href="https://fonts.googleapis.com/css2?family=Roboto:wght@400;700&family=Itim&display=swap">
<style>
  :root {
    --backdrop: #e6e6e6;
    --card-top: #eef8fe;
    --card-mid: #b9dcf3;
    --card-bottom: #5aa3dc;
    --navy: #0f3a66;
    --brand-blue: #3176b5;
    --water-light: #d6eefc;
    --water-deep: #3f8fd0;
    --white: #ffffff;
  }
  * { box-sizing: border-box; margin: 0; padding: 0; }
  html, body { width: 1200px; height: 960px; overflow: hidden; }
  body {
    background: var(--backdrop);
    font-family: "Roboto", Arial, sans-serif;
    position: relative;
  }
  .card {
    position: absolute;
    width: 600px;
    height: 343px;
    background: linear-gradient(180deg, var(--card-top) 0%, var(--card-mid) 45%, var(--card-bottom) 100%);
    overflow: hidden;
  }
  .card--front { left: 302px; top: 125px; }
  .card--back { left: 300px; top: 493px; }
  .splash { position: absolute; top: 0; }
  .splash--front { left: 0; }
  .splash--back { right: 0; }

  .badges { position: absolute; top: 60px; left: 378px; display: flex; gap: 30px; align-items: center; }
  .badge { background: var(--navy); }
  .badge--round { width: 32px; height: 36px; border-radius: 8px; }
  .badge--wide { width: 118px; height: 30px; border-radius: 3px; }

  .services {
    position: absolute; right: 42px; top: 205px;
    list-style: none; text-align: right;
    color: var(--white); font-size: 15px; line-height: 24px;
  }
  .services li { position: relative; padding-right: 0; }
  .services li::after {
    content: ""; position: absolute; right: -14px; top: 10px;
    width: 6px; height: 6px; border-radius: 50%; background: var(--navy);
  }

  .brand {
    position: absolute; left: 100px; top: 92px;
    display: flex; align-items: center; gap: 10px;
  }
  .brand__dot { width: 14px; height: 14px; border-radius: 50%; background: var(--navy); }
  .brand__name { font-family: "Roboto", Arial, sans-serif; font-size: 28px; font-weight: 700; color: var(--navy); }

  .person {
    position: absolute; left: 30px; top: 170px;
    font-family: "Itim", "Comic Sans MS", cursive; font-size: 23px; color: var(--navy); letter-spacing: 0.5px;
  }
  .contacts { position: absolute; left: 30px; top: 209px; color: var(--white); list-style: none; }
  .contacts li { display: flex; align-items: center; gap: 7px; font-size: 17px; height: 21.5px; }
  .contacts .phones { font-weight: 700; font-size: 18.5px; height: 22px; }
  .contacts .sep { margin: 0 10px; font-weight: 400; }
  .icon { width: 14px; height: 14px; flex: none; fill: var(--navy); }
  .icon-at { width: 14px; color: var(--navy); font-size: 17px; font-weight: 700; text-align: center; }
  .abn { position: absolute; left: 50px; top: 307px; font-size: 10px; color: var(--white); }
</style>
</head>
<body>

<section class="card card--front" aria-label="Card front">
  <svg class="splash splash--front" width="380" height="343" viewBox="0 0 380 343" role="img" aria-label="Water wave with bubbles falling down the left edge">
    <defs>
      <linearGradient id="waterFront" x1="0" y1="0" x2="0" y2="1">
        <stop offset="0" stop-color="var(--water-light)"/>
        <stop offset="1" stop-color="var(--water-deep)" stop-opacity="0.55"/>
      </linearGradient>
    </defs>
    <path d="M0 0 H370 C330 40 260 75 170 80 C120 95 110 170 85 240 C70 290 65 320 60 343 H0 Z" fill="url(#waterFront)"/>
  </svg>

  <div class="badges">
    <span class="badge badge--round"></span>
    <span class="badge badge--wide"></span>
  </div>

  <ul class="services">
    <li>Complete Bathroom Renovations &amp; Remodelling</li>
    <li>Professional Service From Concept To Completion</li>
    <li>Highly Skilled &amp; Qualified Tradespeople</li>
    <li>All Work Guaranteed</li>
  </ul>
</section>

<section class="card card--back" aria-label="Card back">
  <svg class="splash splash--back" width="360" height="343" viewBox="0 0 360 343" role="img" aria-label="Water wave with bubbles falling down the right edge">
    <defs>
      <linearGradient id="waterBack" x1="0" y1="0" x2="0" y2="1">
        <stop offset="0" stop-color="var(--water-light)"/>
        <stop offset="1" stop-color="var(--water-deep)" stop-opacity="0.55"/>
      </linearGradient>
    </defs>
    <path d="M10 0 H360 V343 H290 C280 300 270 250 240 200 C200 140 150 110 110 90 C80 60 40 30 10 0 Z" fill="url(#waterBack)"/>
  </svg>

  <div class="brand">
    <span class="brand__dot"></span>
    <span class="brand__name">Crestline Bathrooms</span>
  </div>

  <p class="person">Daniel Morrow</p>

  <ul class="contacts">
    <li class="phones">
      <svg class="icon" viewBox="0 0 24 24"><path d="M6.6 10.8a15.1 15.1 0 0 0 6.6 6.6l2.2-2.2c.3-.3.7-.4 1-.2 1.1.4 2.3.6 3.6.6.6 0 1 .4 1 1V20c0 .6-.4 1-1 1A17 17 0 0 1 3 4c0-.6.4-1 1-1h3.5c.6 0 1 .4 1 1 0 1.3.2 2.5.6 3.6.1.3 0 .7-.2 1z"/></svg>
      0400 318 274<span class="sep">|</span>6200 4159
    </li>
    <li><span class="icon-at">@</span>daniel@crestlinebathrooms.com.au</li>
    <li>
      <svg class="icon" viewBox="0 0 24 24"><circle cx="12" cy="12" r="10"/><path d="M2 12h20M12 2c3 3 3 17 0 20M12 2c-3 3-3 17 0 20" stroke="#fff" stroke-width="1.4" fill="none"/></svg>
      crestlinebathrooms.com.au
    </li>
    <li>
      <svg class="icon" viewBox="0 0 24 24"><path d="M2 5h20v14H2z"/><path d="M2 5l10 8 10-8" stroke="#fff" stroke-width="1.6" fill="none"/></svg>
      PO Box 48 Karrawong 2600
    </li>
  </ul>

  <p class="abn">ABN 12 504 316 927</p>
</section>

</body>
</html>
```